Building company buisness cards

We are looking for a sharp modern new look for our business cards.We are a New Zealand based company that specialises in house and land packages.We have attached a photo of the current logo and would like to see if it can be improved somehow if needed.We are open to any colours but we have chosen Black and White at this stage. Feel free to change the font and make the logo smarter looking.Play with the colours and see what looks best.We want a card that looks so good know one will want to throw it away!

Target Market(s)

Building profesonals, home buyers

Industry/Entity Type

Building

Contact Information for Business Card

Garrick Tenwood
0275390628
garrickt@hartvale.co.nz

Font styles to use
Serif
Sans Serif

Colors

Designer to choose colors to be used in the design.

Requirements
Must have
• Just the logo on one side and details on the other
• Clean simple looking card
Nice to have
• Round corners and detail like raised or spot UV
• Something that stands out
Should not have
• To title needed, Director etc

```html
<!DOCTYPE html>
<html lang="en">
<head>
<meta charset="utf-8">
<title>Hartvale Business Cards</title>
<link href="https://fonts.googleapis.com/css2?family=Work+Sans:wght@400;500;600&display=swap" rel="stylesheet">
<style>
  :root {
    --backdrop: #1b1b1b;
    --card: #262626;
    --card-edge: #303030;
    --ink-light: #e6e6e6;
    --ink-soft: #bdbdbd;
    --ink-mark: #8a8a8a;
    --rule: #9a9a9a;
  }
  * { margin: 0; padding: 0; box-sizing: border-box; }
  html, body {
    width: 1200px;
    height: 900px;
    overflow: hidden;
    background: var(--backdrop);
    font-family: "Work Sans", Arial, sans-serif;
  }
  .stage {
    position: relative;
    width: 1200px;
    height: 900px;
  }
  .card {
    position: absolute;
    left: 270px;
    width: 660px;
    height: 377px;
    background: var(--card);
    border: 1px solid var(--card-edge);
    border-radius: 14px;
    box-shadow: 0 10px 30px rgba(0,0,0,0.45);
  }
  .card-front { top: 52px; }
  .card-back { top: 471px; }

  .brand {
    display: flex;
    align-items: center;
    gap: 14px;
  }
  .brand-name {
    font-weight: 600;
    letter-spacing: 0.01em;
    line-height: 1;
  }
  .brand-dot {
    border-radius: 50%;
    border: 2px solid currentColor;
    flex: none;
  }

  .card-front .brand {
    position: absolute;
    left: 50%;
    top: 50%;
    transform: translate(-50%, -50%);
    color: var(--ink-light);
  }
  .card-front .brand-name { font-size: 64px; }
  .card-front .brand-dot { width: 62px; height: 62px; }

  .card-back .brand {
    position: absolute;
    left: 46px;
    top: 152px;
    color: var(--ink-mark);
  }
  .card-back .brand-name { font-size: 46px; }
  .card-back .brand-dot { width: 44px; height: 44px; }

  .divider {
    position: absolute;
    left: 338px;
    top: 82px;
    width: 1px;
    height: 212px;
    background: var(--rule);
  }

  .details {
    position: absolute;
    left: 372px;
    top: 84px;
    color: var(--ink-soft);
  }
  .person-name {
    font-size: 21px;
    font-weight: 500;
    letter-spacing: 0.08em;
    color: var(--ink-light);
    text-transform: uppercase;
  }
  .person-role {
    font-size: 15px;
    margin-top: 2px;
  }
  .address {
    font-size: 16px;
    line-height: 1.45;
    margin-top: 16px;
    font-style: normal;
  }
  .contact-list {
    list-style: none;
    margin-top: 12px;
  }
  .contact-list li {
    display: flex;
    align-items: center;
    gap: 10px;
    font-size: 16px;
    line-height: 1.6;
  }
  .contact-icon {
    width: 12px;
    height: 12px;
    flex: none;
  }
</style>
</head>
<body>
<main class="stage">
  <section class="card card-front" aria-label="Card front">
    <div class="brand">
      <span class="brand-name">Hartvale</span>
      <span class="brand-dot" aria-hidden="true"></span>
    </div>
  </section>

  <section class="card card-back" aria-label="Card back">
    <div class="brand">
      <span class="brand-name">Hartvale</span>
      <span class="brand-dot" aria-hidden="true"></span>
    </div>
    <div class="divider"></div>
    <div class="details">
      <p class="person-name">Garrick Tenwood</p>
      <p class="person-role">Director</p>
      <address class="address">52b Kerrow Lane,<br>Ashby, NZ, 8042</address>
      <ul class="contact-list">
        <li>
          <svg class="contact-icon" viewBox="0 0 12 12" aria-hidden="true"><path d="M2.5 1 L4.5 1 L5.2 3.4 L4 4.4 Q5 6.8 7.6 8 L8.6 6.8 L11 7.5 L11 9.5 Q10.5 11 9 11 Q1 10 1 2.8 Q1 1.2 2.5 1 Z" fill="currentColor"/></svg>
          <span>0275390628</span>
        </li>
        <li>
          <svg class="contact-icon" viewBox="0 0 12 12" aria-hidden="true"><rect x="0.8" y="2.3" width="10.4" height="7.4" fill="none" stroke="currentColor" stroke-width="1.1"/><path d="M1 2.6 L6 6.6 L11 2.6" fill="none" stroke="currentColor" stroke-width="1.1"/></svg>
          <span>garrickt@hartvale.co.nz</span>
        </li>
        <li>
          <svg class="contact-icon" viewBox="0 0 12 12" aria-hidden="true"><circle cx="6" cy="6" r="5" fill="none" stroke="currentColor" stroke-width="1"/><ellipse cx="6" cy="6" rx="2.2" ry="5" fill="none" stroke="currentColor" stroke-width="0.9"/><path d="M1 6 H11 M2 3.5 H10 M2 8.5 H10" stroke="currentColor" stroke-width="0.8"/></svg>
          <span>www.hartvale.co.nz</span>
        </li>
      </ul>
    </div>
  </section>
</main>
</body>
</html>
```